Bry7Legal Letterhead

Need a new letterhead for my law firm.
IDENTIFYING INFORMATION BELOW:
Anselmo R Quintara III
Attorney at Law
Address: 2847 Larkspur Blvd, Ste 300, Dallas, TX 75204
Phone: 877-482-6017
Fax: 469-738-1452
Email: bry@bry7legal.example
Website: www.bry7legal.example

Colors
0054AA
0677BA
7BADD7
CADEEF
E8F1F8

Requirements
Must have
• Logo needs to be on the letterhead, along with identifying information which is included in the project description.

```html
<!DOCTYPE html>
<html lang="en">
<head>
<meta charset="utf-8">
<title>Bry7Legal Letterhead</title>
<link href="https://fonts.googleapis.com/css2?family=Open+Sans:wght@400;700;800&display=swap" rel="stylesheet">
<style>
  :root {
    --backdrop: #d8dcdf;
    --paper: #ffffff;
    --ink: #111111;
    --brand-blue: #0677ba;
    --muted: #7a7f84;
  }
  * { margin: 0; padding: 0; box-sizing: border-box; }
  html, body {
    width: 1200px; height: 784px; overflow: hidden;
    background: var(--backdrop);
    font-family: "Open Sans", Arial, sans-serif;
  }
  .letterhead {
    position: absolute; left: 320px; top: 30px;
    width: 560px; height: 724px;
    background: var(--paper);
    box-shadow: 0 2px 10px rgba(0,0,0,.12);
    overflow: hidden;
  }
  .edge { position: absolute; left: 0; width: 100%; height: 30px; display: block; }
  .edge--top { top: 0; }
  .edge--bottom { bottom: 0; }
  .brand { position: absolute; left: 38px; top: 30px; }
  .brand__name {
    font-weight: 800; font-size: 34px; line-height: 1;
    color: var(--ink); letter-spacing: 1px; text-transform: uppercase;
  }
  .brand__tagline {
    margin-top: 4px; font-size: 10.5px; letter-spacing: 2.4px;
    color: var(--ink); text-transform: uppercase;
  }
  .contact {
    position: absolute; right: 34px; top: 118px;
    padding-left: 8px; border-left: 1px solid #cfd3d6;
    font-size: 7.6px; line-height: 1.55; color: var(--muted);
  }
  .contact__address { font-weight: 700; color: var(--ink); }
  .contact__row { display: flex; align-items: center; gap: 3px; }
  .contact__row svg { width: 7px; height: 7px; fill: var(--ink); flex: none; }
  .contact__gap { width: 4px; }
</style>
</head>
<body>
  <main class="letterhead">
    <svg class="edge edge--top" viewBox="0 0 560 30" preserveAspectRatio="none" aria-hidden="true">
      <rect x="0" y="0" width="560" height="5" fill="#111111"/>
      <rect x="0" y="9" width="560" height="2.5" fill="#0677ba"/>
    </svg>

    <header class="brand">
      <div class="brand__name">Bry7Legal</div>
      <div class="brand__tagline">Counsel in Motion</div>
    </header>

    <address class="contact" style="font-style:normal">
      <div class="contact__address">2847 Larkspur Blvd, Ste 300, Dallas, TX 75204</div>
      <div class="contact__row">
        <svg viewBox="0 0 10 10"><path d="M2 0h2l1 3-1.5 1a6 6 0 0 0 2.5 2.5L7 5l3 1v2a2 2 0 0 1-2 2A8 8 0 0 1 0 2a2 2 0 0 1 2-2z"/></svg>
        <span>877-482-6017</span><span class="contact__gap"></span>
        <svg viewBox="0 0 10 10"><path d="M2 0h6v3H2zM0 4h10v5H0zM2 7h6v3H2z"/></svg>
        <span>469-738-1452</span>
      </div>
      <div class="contact__row">
        <svg viewBox="0 0 10 10"><path d="M0 2h10v6H0zM0 2l5 3.5L10 2" stroke="#fff" stroke-width=".8"/></svg>
        <span>bry@bry7legal.example</span><span class="contact__gap"></span>
        <svg viewBox="0 0 10 10"><circle cx="5" cy="5" r="5"/><path d="M0 5h10M5 0c-3 3-3 7 0 10M5 0c3 3 3 7 0 10" stroke="#fff" stroke-width=".7" fill="none"/></svg>
        <span>www.bry7legal.example</span>
      </div>
    </address>

    <svg class="edge edge--bottom" viewBox="0 0 560 30" preserveAspectRatio="none" aria-hidden="true">
      <path d="M0 18.5H190l5 -2.5H560v2.5H197l-5 2.5H0z" fill="#0677ba"/>
      <path d="M0 22H190l8 -3H380l8 3H560v8H0z" fill="#111111"/>
    </svg>
  </main>
</body>
</html>
```